BOLD & MINIMALIST DESIGN NEEDED

We want a very bold but minimalistic business card design that is impactful and utilizes both sides of the business card. Our current logo is included for your use.

We want bold fonts and good use of negative space. We don't want the logo to overpower the design.

Target Market(s)

Professionals who are building new commercial buildings.

Industry/Entity Type

Construction

Contact Information for Business Card

Name, Title, email, office phone, cell phone, website

Font styles to use
Serif
Sans Serif

Requirements
Must have
• Bold design!

```html
<!DOCTYPE html>
<html lang="en">
<head>
<meta charset="utf-8">
<title>Ridgemont Design + Build – Business Card</title>
<link rel="stylesheet" href="https://fonts.googleapis.com/css2?family=Montserrat:wght@300;400;700;800&display=swap">
<style>
  :root {
    --backdrop: #dcdcdc;
    --card-black: #0c0d0f;
    --card-white: #ffffff;
    --accent-green: #94cc55;
    --ink: #111111;
    --muted: #777777;
    --title-grey: #6e6e6e;
  }
  * { margin: 0; padding: 0; box-sizing: border-box; }
  html, body {
    width: 1200px; height: 1200px; overflow: hidden;
    background: var(--backdrop);
    font-family: "Montserrat", Arial, sans-serif;
  }
  .canvas { position: relative; width: 1200px; height: 1200px; }

  .card {
    position: absolute; left: 179px; width: 861px; height: 496px;
    background: var(--card-black); overflow: hidden;
  }
  .card--front { top: 84px; }
  .card--back { top: 622px; }

  .brand-name {
    font-family: "Montserrat", Arial, sans-serif;
    font-weight: 800;
    color: var(--card-white);
    text-transform: uppercase;
    line-height: 1.05;
    letter-spacing: 1px;
  }
  .card--front .brand-name {
    position: absolute; left: 0; right: 0; top: 190px;
    text-align: center; font-size: 46px;
  }
  .brand-name .brand-line { display: block; }
  .brand-name .brand-line--small { font-size: 0.5em; letter-spacing: 8px; margin-top: 6px; }

  .card--back .brand-name {
    position: absolute; left: 43px; top: 66px; width: 342px;
    text-align: center; font-size: 38px;
  }

  .back-shape { position: absolute; inset: 0; width: 100%; height: 100%; }

  .brand-badge {
    position: absolute; left: 528px; top: 160px; width: 290px;
    display: flex; align-items: center; justify-content: center; gap: 12px;
  }
  .brand-badge .brand-square { width: 26px; height: 26px; background: var(--accent-green); }
  .brand-badge .brand-name { position: static; width: auto; color: var(--ink); font-size: 34px; }

  .person {
    position: absolute; right: 48px; top: 288px; text-align: right;
  }
  .person-name { font-weight: 700; font-size: 34px; color: var(--ink); letter-spacing: 0.5px; }
  .person-title { font-weight: 400; font-size: 24px; color: var(--title-grey); letter-spacing: 1.5px; margin-top: 2px; }

  .contact {
    position: absolute; top: 404px;
    font-weight: 300; font-size: 23px; color: var(--muted); letter-spacing: 1px;
  }
  .contact li { list-style: none; display: flex; align-items: center; gap: 12px; height: 36px; }
  .contact svg { width: 24px; height: 24px; flex: none; }
  .contact--phones { left: 156px; }
  .contact--web { right: 46px; }
  .contact--web li { justify-content: flex-end; }
  .accent { color: var(--accent-green); }
</style>
</head>
<body>
<div class="canvas">

  <section class="card card--front" aria-label="Card front">
    <div class="brand-name">
      <span class="brand-line">Ridgemont</span>
      <span class="brand-line brand-line--small">Design + Build</span>
    </div>
  </section>

  <section class="card card--back" aria-label="Card back">
    <svg class="back-shape" viewBox="0 0 1387 797" preserveAspectRatio="none" aria-hidden="true">
      <polygon points="0,649 1085,52 1387,214 1387,222 1083,92 0,656" fill="#94cc55"/>
      <polygon points="0,656 1083,92 1387,222 1387,797 0,797" fill="#ffffff"/>
    </svg>

    <div class="brand-name">
      <span class="brand-line">Ridgemont</span>
      <span class="brand-line brand-line--small">Design + Build</span>
    </div>

    <div class="brand-badge">
      <span class="brand-square"></span>
      <span class="brand-name">Ridgemont</span>
    </div>

    <div class="person">
      <p class="person-name">Name Surename</p>
      <p class="person-title">Director</p>
    </div>

    <ul class="contact contact--phones">
      <li>
        <svg viewBox="0 0 24 24" aria-hidden="true"><path d="M6.6 10.8a15 15 0 0 0 6.6 6.6l2.2-2.2c.3-.3.7-.4 1-.2 1.1.4 2.3.6 3.6.6.6 0 1 .4 1 1V20c0 .6-.4 1-1 1A17 17 0 0 1 3 4c0-.6.4-1 1-1h3.5c.6 0 1 .4 1 1 0 1.3.2 2.5.6 3.6.1.3 0 .7-.2 1z" fill="#111"/></svg>
        <span>555-014-2200</span>
      </li>
      <li>
        <svg viewBox="0 0 24 24" aria-hidden="true"><path d="M2 9c0-3 4-5 10-5s10 2 10 5v2h-5V8.5H7V11H2z" fill="#111"/><rect x="4" y="12" width="16" height="9" rx="1.5" fill="#111"/><circle cx="12" cy="16.5" r="2.2" fill="#fff"/></svg>
        <span>555-014-2200</span>
      </li>
    </ul>

    <ul class="contact contact--web">
      <li>
        <span>info@r-d-b.com</span>
        <svg viewBox="0 0 24 24" aria-hidden="true"><rect x="2" y="5" width="20" height="14" fill="#111"/><path d="M2.5 5.5 12 13l9.5-7.5M2.5 18.5l7-6.5M21.5 18.5l-7-6.5" stroke="#fff" stroke-width="1.4" fill="none"/></svg>
      </li>
      <li>
        <span>www.<span class="accent">r-d-b</span>.com</span>
        <svg viewBox="0 0 24 24" aria-hidden="true"><g fill="none" stroke="#111" stroke-width="1.6"><circle cx="12" cy="12" r="10"/><ellipse cx="12" cy="12" rx="4.5" ry="10"/><path d="M2 12h20M3.5 7h17M3.5 17h17"/></g></svg>
      </li>
    </ul>
  </section>

</div>
</body>
</html>
```